Redesign of business card for Cedar Ridge Mechanical

We are looking for a new design for our business cards for Cedar Ridge Mechanical. We are a plumbing & HVAC construction company, operating on the West Coast of Canada and USA. Logo attached.
Industry/Entity Type
Construction - Plumbing & HVAC
Contact Information for Business Card
Name, address, phone numbers, email, website address
Look and feel
Each slider illustrates characteristics of the customer's brand and the style your logo design should communicate.

```html
<!DOCTYPE html>
<html lang="en">
<head>
<meta charset="UTF-8">
<title>Cedar Ridge Mechanical – Business Card</title>
<link href="https://fonts.googleapis.com/css2?family=Montserrat:wght@400;700&family=Oswald:wght@400;500&display=swap" rel="stylesheet">
<style>
  :root {
    --backdrop: #2e2e2e;
    --card-dark: #000000;
    --card-light: #ffffff;
    --ink-light: #ffffff;
    --ink-dark: #111111;
    --ink-muted: #222222;
  }
  * { margin: 0; padding: 0; box-sizing: border-box; }
  html, body {
    width: 1200px;
    height: 689px;
    overflow: hidden;
    background: var(--backdrop);
  }
  .canvas {
    position: relative;
    width: 1200px;
    height: 689px;
    display: flex;
    align-items: center;
    justify-content: center;
    gap: 40px;
  }
  .card {
    position: relative;
    width: 520px;
    height: 297px;
    overflow: hidden;
  }

  /* Front */
  .card--front {
    background: var(--card-dark);
    display: flex;
    align-items: center;
    justify-content: center;
  }
  .front-wordmark {
    font-family: 'Oswald', sans-serif;
    font-weight: 500;
    font-size: 34px;
    letter-spacing: 3px;
    text-transform: uppercase;
    color: var(--ink-light);
  }

  /* Back */
  .card--back {
    background: var(--card-light);
    font-family: 'Montserrat', sans-serif;
    color: var(--ink-dark);
  }
  .back-wordmark {
    position: absolute;
    top: 30px;
    right: 32px;
    font-family: 'Oswald', sans-serif;
    font-weight: 500;
    font-size: 13px;
    letter-spacing: 1.5px;
    text-transform: uppercase;
    color: var(--ink-dark);
  }
  .person {
    position: absolute;
    left: 40px;
    top: 122px;
    width: 190px;
    text-align: right;
  }
  .person__name {
    font-weight: 700;
    font-size: 22px;
    letter-spacing: 0.5px;
    text-transform: uppercase;
  }
  .person__role {
    font-weight: 400;
    font-size: 13px;
    margin-top: 2px;
    color: var(--ink-muted);
  }
  .divider {
    position: absolute;
    left: 250px;
    top: 112px;
    width: 1px;
    height: 68px;
    background: var(--ink-dark);
  }
  .contacts {
    position: absolute;
    left: 268px;
    top: 112px;
    list-style: none;
    font-size: 13px;
    line-height: 22px;
  }
  .contacts li {
    display: flex;
    align-items: center;
    gap: 8px;
  }
  .contacts svg {
    width: 11px;
    height: 11px;
    fill: var(--ink-dark);
    flex: none;
  }
  .address {
    position: absolute;
    right: 32px;
    bottom: 34px;
    font-size: 13px;
    color: var(--ink-muted);
  }
</style>
</head>
<body>
<main class="canvas">
  <section class="card card--front">
    <p class="front-wordmark">Cedar Ridge Mechanical</p>
  </section>

  <section class="card card--back">
    <p class="back-wordmark">Cedar Ridge Mechanical</p>

    <div class="person">
      <h1 class="person__name">Daniel Hart</h1>
      <p class="person__role">Managing Director</p>
    </div>

    <span class="divider"></span>

    <ul class="contacts">
      <li>
        <svg viewBox="0 0 24 24" aria-hidden="true"><path d="M6.6 10.8a15.1 15.1 0 0 0 6.6 6.6l2.2-2.2a1 1 0 0 1 1-.25 11.4 11.4 0 0 0 3.6.57 1 1 0 0 1 1 1V20a1 1 0 0 1-1 1A17 17 0 0 1 3 4a1 1 0 0 1 1-1h3.5a1 1 0 0 1 1 1c0 1.25.2 2.45.57 3.57a1 1 0 0 1-.25 1z"/></svg>
        123 456 789
      </li>
      <li>
        <svg viewBox="0 0 24 24" aria-hidden="true"><path d="M2 5h20v14H2zm2 2v.5l8 5 8-5V7zm0 2.8V17h16V9.8l-8 5z"/></svg>
        info@youremail.com
      </li>
      <li>
        <svg viewBox="0 0 24 24" aria-hidden="true"><circle cx="12" cy="12" r="10"/></svg>
        www.yourwebsite.com
      </li>
    </ul>

    <p class="address">Your address, City State, Zip 1234</p>
  </section>
</main>
</body>
</html>
```